Website for BrightlineLabs presentation

We need a new website, ideally as a wordpress there, for BrightlineLabs - we focus on machine learning, big data, data science and data analytics. This website should have two main sections - team presentation, introduction and offered services as static pages, and a blog section.

Target Market(s)

Companies which would like to hire the consultants for data science

Industry/Entity Type

Data Service

Font styles to use
Sans Serif

Colors

Designer to choose colors to be used in the design.

Requirements
Must have
• Wordpress template, blog and presentation pages, nice background images, incorporate the existing logo from brief
Nice to have
• match the word and ppt existing templates for brightline labs

```html
<!DOCTYPE html>
<html lang="en">
<head>
<meta charset="utf-8">
<title>BrightlineLabs — Data Science Consultants</title>
<link href="https://fonts.googleapis.com/css2?family=Montserrat:wght@500;600;700;800&family=Open+Sans:wght@400;600;700&display=swap" rel="stylesheet">
<style>
:root{
  --blue:#1e73e8;
  --blue-deep:#1659b8;
  --blue-mid:#2d82e6;
  --blue-soft:#4d9bef;
  --blue-pale:#74b3f3;
  --navy:#07101e;
  --ink:#1d2533;
  --text:#6b7480;
  --ghost:#eef0f3;
  --line:#d9e6f7;
  --white:#ffffff;
}
*{box-sizing:border-box;margin:0;padding:0}
html,body{width:1200px;height:4852px;overflow:hidden}
body{position:relative;background:var(--white);font-family:"Open Sans",Arial,sans-serif;color:var(--text)}
.abs{position:absolute}
h1,h2,h3,h4,.nav a,.btn{font-family:"Montserrat",Arial,sans-serif}

/* header */
.site-header{position:absolute;left:0;top:0;width:1200px;height:120px;background:var(--white)}
.brand{position:absolute;left:100px;top:22px;display:flex;align-items:center;gap:12px}
.brand-mark{width:40px;height:40px;background:var(--blue)}
.brand-name{font-family:"Montserrat",Arial,sans-serif;font-weight:800;font-size:20px;line-height:22px;color:var(--blue-deep);width:140px}
.nav{position:absolute;top:46px;left:460px;display:flex;gap:0}
.nav a{display:block;font-size:13px;font-weight:600;color:var(--ink);text-decoration:none;padding:0 22px;position:relative}
.nav a.active{color:var(--blue)}
.nav a.active::after{content:"";position:absolute;left:22px;right:22px;top:24px;height:2px;background:var(--blue)}
.search{position:absolute;left:1086px;top:46px}

/* hero */
.hero{position:absolute;left:0;top:120px;width:1200px;height:760px;background:radial-gradient(circle at 85% 25%,#1d4f8f 0%,#0c2446 30%,var(--navy) 65%)}
.hero-title{position:absolute;left:0;width:1200px;top:230px;text-align:center;color:var(--white);font-size:56px;font-weight:800;letter-spacing:1px}
.hero-sub{position:absolute;left:0;width:1200px;top:318px;text-align:center;color:#cdd8e8;font-size:16px}
.btn{display:inline-block;font-size:13px;font-weight:700;text-decoration:none;border-radius:24px}
.hero .btn{position:absolute;left:522px;top:378px;width:156px;height:50px;line-height:50px;text-align:center;background:var(--blue);color:var(--white)}
.hero-arrow{position:absolute;top:318px;width:36px;height:36px;border:2px solid rgba(255,255,255,.6);border-radius:50%}

/* section headings */
.heading{position:absolute;left:0;width:1200px;text-align:center}
.heading .ghost{position:absolute;left:0;width:1200px;top:-14px;font-family:"Montserrat",Arial,sans-serif;font-weight:800;font-size:60px;color:var(--ghost);letter-spacing:2px}
.heading h2{position:relative;font-size:36px;font-weight:800;color:var(--ink)}
.heading h2 span{color:var(--blue)}
.heading .bar{position:relative;width:50px;height:4px;background:var(--blue);margin:16px auto 0}

/* about */
.about-photo{position:absolute;left:104px;top:1019px;width:511px;height:404px;background:linear-gradient(135deg,#c9d4e0,#8b9db3 55%,#5e6f86)}
.play{position:absolute;left:295px;top:1170px}
.about-box{position:absolute;left:598px;top:993px;width:502px;height:453px;border:4px solid var(--blue);background:var(--white);padding:46px 48px}
.about-box h2{font-size:38px;font-weight:800;color:var(--ink);position:relative}
.about-box h2 span{color:var(--blue)}
.about-box h2 em{font-style:normal;color:var(--ghost);position:absolute;left:196px;top:0}
.about-box p{margin-top:34px;font-size:13px;line-height:25px;color:var(--text)}
.about-box .btn{margin-top:28px;width:124px;height:44px;line-height:40px;text-align:center;border:2px solid var(--blue);color:var(--blue)}

/* services */
.services{position:absolute;left:0;top:1598px;width:1200px;height:414px;display:flex}
.service{flex:1;padding:42px 44px 0;text-align:center;color:var(--white)}
.service:nth-child(1){background:var(--blue-deep)}
.service:nth-child(2){background:var(--blue-mid)}
.service:nth-child(3){background:var(--blue-soft)}
.service:nth-child(4){background:var(--blue-pale)}
.service h3{margin-top:30px;font-size:15px;font-weight:700;letter-spacing:.5px}
.service p{margin-top:16px;font-size:12.5px;line-height:24px;color:rgba(255,255,255,.92)}

/* team */
.team{position:absolute;left:104px;top:2340px;width:996px;display:flex}
.member{flex:1;text-align:center}
.member .portrait{width:170px;height:170px;border-radius:50%;margin:0 auto;background:linear-gradient(160deg,#d8dde4,#7c8796)}
.member h4{margin-top:28px;font-size:18px;font-weight:600;color:var(--ink)}
.member p{margin:14px auto 0;width:200px;font-size:12.5px;line-height:22px}
.socials{margin-top:14px;display:flex;justify-content:center;gap:8px}
.socials i{width:28px;height:28px;border-radius:50%;background:var(--blue-deep);display:block}
.socials i+i{background:var(--blue-soft)}

/* blog */
.blog-bg{position:absolute;left:0;top:2830px}
.heading.on-blue h2{color:var(--white)}
.heading.on-blue .ghost{color:rgba(255,255,255,.12)}
.heading.on-blue .bar{background:var(--white)}
.posts{position:absolute;left:104px;top:3203px;width:996px;display:flex;gap:26px}
.post{flex:1;background:var(--white);height:307px;position:relative}
.post .thumb{height:190px;background:linear-gradient(150deg,#0f2d58,#1f6fd0 60%,#57a6f2)}
.post .plus{position:absolute;right:14px;top:172px;width:38px;height:38px;border-radius:50%;background:var(--white);border:2px solid var(--blue)}
.post h4{padding:26px 18px 0;font-size:16px;font-weight:700;color:var(--ink)}
.post p{padding:10px 18px 0;font-size:12px;line-height:20px}
.slider-arrow{position:absolute;top:3338px}

/* testimonials */
.quotes{position:absolute;left:104px;top:4028px;width:996px;display:flex;gap:22px}
.quote{flex:1;height:194px;border:2px solid var(--line);text-align:center;padding:18px 30px 0}
.quote .mark{font-family:"Montserrat",Arial,sans-serif;font-weight:800;font-size:46px;line-height:40px;color:var(--blue)}
.quote p{margin-top:12px;font-size:12.5px;line-height:22px;font-style:italic;color:var(--text)}
.authors{position:absolute;left:104px;top:4245px;width:996px;display:flex;gap:22px}
.author{flex:1;display:flex;align-items:center;justify-content:center;gap:12px}
.author .avatar{width:46px;height:46px;border-radius:50%;background:linear-gradient(150deg,#d9c0a8,#8a6e58)}
.author b{display:block;font-family:"Montserrat",Arial,sans-serif;font-weight:600;font-size:16px;color:var(--ink)}
.author small{display:block;font-size:11px;color:var(--text)}
.client{font-family:"Open Sans",Arial,sans-serif;font-weight:700;font-size:14px;color:var(--ink);margin-left:10px}

/* footer */
.footer-bg{position:absolute;left:0;top:4420px}
.footer-social{position:absolute;left:0;width:1200px;top:4628px;display:flex;justify-content:center;gap:12px}
.footer-social i{width:46px;height:46px;border-radius:50%;border:2px solid var(--white);display:block}
.footer-links{position:absolute;left:0;width:1200px;top:4706px;text-align:center;font-size:14px;color:var(--white)}
.footer-links span{margin:0 10px;color:#8a93a0}
.copyright{position:absolute;left:0;width:1200px;top:4750px;text-align:center;font-size:12px;color:var(--white)}
.legal{position:absolute;left:0;width:1200px;top:4786px;text-align:center;font-size:12px;color:var(--white)}
.legal span{margin:0 8px;color:#8a93a0}
</style>
</head>
<body>

<header class="site-header">
  <div class="brand"><div class="brand-mark"></div><div class="brand-name">BRIGHTLINE LABS</div></div>
  <nav class="nav">
    <a class="active" href="#">HOME</a><a href="#">ABOUT US</a><a href="#">SERVICES</a><a href="#">BLOG</a><a href="#">TEAM</a><a href="#">CONTACT US</a>
  </nav>
  <svg class="search" width="16" height="16" viewBox="0 0 16 16" aria-label="Search"><circle cx="6.5" cy="6.5" r="5" fill="none" stroke="#1e73e8" stroke-width="2"/><line x1="10.5" y1="10.5" x2="15" y2="15" stroke="#1e73e8" stroke-width="2"/></svg>
</header>

<section class="hero" role="img" aria-label="Dark blue network background with glowing hexagon grid">
  <h1 class="hero-title">BRIGHTLINE LABS</h1>
  <p class="hero-sub">Sed perspiciatis undeste natus voluptatem accusantium doloremque</p>
  <a class="btn" href="#">READ MORE</a>
  <svg class="hero-arrow" style="left:56px" viewBox="0 0 36 36"><polyline points="20,12 14,18 20,24" fill="none" stroke="#fff" stroke-width="2"/></svg>
  <svg class="hero-arrow" style="left:1106px" viewBox="0 0 36 36"><polyline points="16,12 22,18 16,24" fill="none" stroke="#fff" stroke-width="2"/></svg>
</section>
<svg class="abs" style="left:0;top:600px" width="1200" height="290" viewBox="0 0 1200 290">
  <polygon points="0,273 1200,47 1200,290 0,290" fill="#fff"/>
  <polygon points="0,258 1200,32 1200,47 0,273" fill="#1e73e8"/>
  <circle cx="600" cy="158" r="22" fill="#fff" stroke="#1e73e8" stroke-width="2"/>
  <polyline points="592,152 600,160 608,152" fill="none" stroke="#1e73e8" stroke-width="2"/>
  <polyline points="592,159 600,167 608,159" fill="none" stroke="#1e73e8" stroke-width="2"/>
</svg>

<!-- about -->
<div class="about-photo" role="img" aria-label="Photo of a team reviewing charts on a computer screen"></div>
<svg class="play" width="84" height="84" viewBox="0 0 84 84" aria-label="Play video"><circle cx="42" cy="42" r="38" fill="none" stroke="#fff" stroke-width="3"/><polygon points="34,26 60,42 34,58" fill="#fff"/></svg>
<section class="about-box">
  <h2>ABOUT <span>US</span><em>US</em></h2>
  <p>Sed ut perspiciatis unde omnis iste natus error sit voluptatem accusantium doloremque laudantium, totam rem aperiam, eaque ipsa quae ab illo inventore veritatis et quasi architecto beatae vitae dicta sunt explicabo. Nemo enim ipsam voluptatem quia voluptas sit aspernatur aut odit aut fugit, sed quia consequuntur magni dolores eos qui ratione sequi nesciunt neque porro quisquam.</p>
  <a class="btn" href="#">READ MORE</a>
</section>

<!-- services -->
<section class="services">
  <div class="service">
    <svg width="56" height="56" viewBox="0 0 56 56"><circle cx="28" cy="28" r="24" fill="none" stroke="#fff" stroke-width="2"/><ellipse cx="28" cy="28" r="1" rx="10" ry="24" fill="none" stroke="#fff" stroke-width="2"/><line x1="4" y1="28" x2="52" y2="28" stroke="#fff" stroke-width="2"/></svg>
    <h3>BIG DATA</h3>
    <p>Sed ut perspiciatis unde omnis iste natus error sit voluptatem accusantium doloremque laudantium totam numquam eius modi tempora incidunt numquam eius modi tempora incidunt ut labore dolore.</p>
  </div>
  <div class="service">
    <svg width="56" height="56" viewBox="0 0 56 56"><rect x="14" y="14" width="28" height="28" rx="4" fill="none" stroke="#fff" stroke-width="2"/><g stroke="#fff" stroke-width="2"><line x1="22" y1="6" x2="22" y2="14"/><line x1="34" y1="6" x2="34" y2="14"/><line x1="22" y1="42" x2="22" y2="50"/><line x1="34" y1="42" x2="34" y2="50"/><line x1="6" y1="22" x2="14" y2="22"/><line x1="6" y1="34" x2="14" y2="34"/><line x1="42" y1="22" x2="50" y2="22"/><line x1="42" y1="34" x2="50" y2="34"/></g></svg>
    <h3>MACHINE LEARNING</h3>
    <p>Sed ut perspiciatis unde omnis iste natus error sit voluptatem accusantium doloremque laudantium totam numquam eius modi tempora incidunt numquam eius modi tempora incidunt ut labore dolore.</p>
  </div>
  <div class="service">
    <svg width="56" height="56" viewBox="0 0 56 56"><circle cx="24" cy="24" r="16" fill="none" stroke="#fff" stroke-width="2"/><line x1="36" y1="36" x2="50" y2="50" stroke="#fff" stroke-width="3"/><polyline points="16,28 22,20 27,25 32,18" fill="none" stroke="#fff" stroke-width="2"/></svg>
    <h3>DATA SCIENCE</h3>
    <p>Sed ut perspiciatis unde omnis iste natus error sit voluptatem accusantium doloremque laudantium totam numquam eius modi tempora incidunt numquam eius modi tempora incidunt ut labore dolore.</p>
  </div>
  <div class="service">
    <svg width="56" height="56" viewBox="0 0 56 56"><g fill="none" stroke="#fff" stroke-width="2"><rect x="8" y="32" width="8" height="16"/><rect x="22" y="24" width="8" height="24"/><rect x="36" y="16" width="8" height="32"/><polyline points="8,22 20,14 30,18 46,6"/></g></svg>
    <h3>DATA ANALYTICS</h3>
    <p>Sed ut perspiciatis unde omnis iste natus error sit voluptatem accusantium doloremque laudantium totam numquam eius modi tempora incidunt numquam eius modi tempora incidunt ut labore dolore.</p>
  </div>
</section>

<!-- team -->
<div class="heading" style="top:2168px">
  <div class="ghost">TEAM PRESENTATION</div>
  <h2>TEAM <span>PRESENTATION</span></h2>
  <div class="bar"></div>
</div>
<section class="team">
  <div class="member"><div class="portrait" role="img" aria-label="Portrait photo of team member"></div><h4>COMMODI</h4><p>Quis autem vel eum iure reprehenderit qui in ea voluptate velit esse quam nihil molestiae consequatur illum qui dolorem eum fugiat quo.</p><div class="socials"><i aria-label="Social profile"></i><i aria-label="Social profile"></i></div></div>
  <div class="member"><div class="portrait" role="img" aria-label="Portrait photo of team member"></div><h4>NEMO ENIM</h4><p>Quis autem vel eum iure reprehenderit qui in ea voluptate velit esse quam nihil molestiae consequatur illum qui dolorem eum fugiat quo.</p><div class="socials"><i aria-label="Social profile"></i><i aria-label="Social profile"></i></div></div>
  <div class="member"><div class="portrait" role="img" aria-label="Portrait photo of team member"></div><h4>VOLUPTATEM</h4><p>Quis autem vel eum iure reprehenderit qui in ea voluptate velit esse quam nihil molestiae consequatur illum qui dolorem eum fugiat quo.</p><div class="socials"><i aria-label="Social profile"></i><i aria-label="Social profile"></i></div></div>
  <div class="member"><div class="portrait" role="img" aria-label="Portrait photo of team member"></div><h4>QUISQUAM</h4><p>Quis autem vel eum iure reprehenderit qui in ea voluptate velit esse quam nihil molestiae consequatur illum qui dolorem eum fugiat quo.</p><div class="socials"><i aria-label="Social profile"></i><i aria-label="Social profile"></i></div></div>
</section>

<!-- blog -->
<svg class="blog-bg" width="1200" height="960" viewBox="0 0 1200 960" role="img" aria-label="Blue technology background with faint data graphics">
  <defs><linearGradient id="blogGrad" x1="0" y1="0" x2="1" y2="1"><stop offset="0" stop-color="#3f93ee"/><stop offset=".6" stop-color="#1e73e8"/><stop offset="1" stop-color="#1659b8"/></linearGradient></defs>
  <polygon points="0,195 1200,0 1200,760 0,955" fill="url(#blogGrad)"/>
</svg>
<div class="heading on-blue" style="top:3058px">
  <div class="ghost">BLOG POSTS</div>
  <h2>BLOG POSTS</h2>
  <div class="bar"></div>
</div>
<svg class="slider-arrow" style="left:34px" width="20" height="36" viewBox="0 0 20 36"><polyline points="16,4 4,18 16,32" fill="none" stroke="#fff" stroke-width="2"/></svg>
<svg class="slider-arrow" style="left:1146px" width="20" height="36" viewBox="0 0 20 36"><polyline points="4,4 16,18 4,32" fill="none" stroke="#fff" stroke-width="2"/></svg>
<section class="posts">
  <article class="post"><div class="thumb" role="img" aria-label="Blog image: digital network graphic"></div><span class="plus"></span><h4>Cum soluta</h4><p>Naque earum rerum hic tenetura sapiente delectus.</p></article>
  <article class="post"><div class="thumb" role="img" aria-label="Blog image: artificial intelligence graphic"></div><span class="plus"></span><h4>Praesentium</h4><p>Naque earum rerum hic tenetura sapiente delectus.</p></article>
  <article class="post"><div class="thumb" role="img" aria-label="Blog image: machine learning concept on screen"></div><span class="plus"></span><h4>Voluptatum</h4><p>Naque earum rerum hic tenetura sapiente delectus.</p></article>
  <article class="post"><div class="thumb" role="img" aria-label="Blog image: glowing digital brain"></div><span class="plus"></span><h4>Quos dolores</h4><p>Naque earum rerum hic tenetura sapiente delectus.</p></article>
</section>

<!-- testimonials -->
<div class="heading" style="top:3893px">
  <div class="ghost">CLIENTS TESTIMONIALS</div>
  <h2>CLIENT <span>TESTIMONIALS</span></h2>
  <div class="bar"></div>
</div>
<section class="quotes">
  <blockquote class="quote"><div class="mark">&ldquo;</div><p>In ullamcorper est eget tempor cursus neque mi consectetuer mi a ultrices massa est sed nisl. Class aptent taciti sociosqu ad litora torquent per conubia nostra.</p></blockquote>
  <blockquote class="quote"><div class="mark">&ldquo;</div><p>In ullamcorper est eget tempor cursus neque mi consectetuer mi a ultrices massa est sed nisl. Class aptent taciti sociosqu ad litora torquent per conubia nostra.</p></blockquote>
  <blockquote class="quote"><div class="mark">&ldquo;</div><p>In ullamcorper est eget tempor cursus neque mi consectetuer mi a ultrices massa est sed nisl. Class aptent taciti sociosqu ad litora torquent per conubia nostra.</p></blockquote>
</section>
<section class="authors">
  <div class="author"><div class="avatar" role="img" aria-label="Client photo"></div><div><b>By Author</b><small>City, Location</small></div><span class="client">Northvale</span></div>
  <div class="author"><div class="avatar" role="img" aria-label="Client photo"></div><div><b>By Author</b><small>City, Location</small></div><span class="client">Corvane</span></div>
  <div class="author"><div class="avatar" role="img" aria-label="Client photo"></div><div><b>By Author</b><small>City, Location</small></div><span class="client">Talmora</span></div>
</section>

<!-- footer -->
<svg class="footer-bg" width="1200" height="432" viewBox="0 0 1200 432">
  <polygon points="0,125 1200,12 1200,432 0,432" fill="#07101e"/>
  <polygon points="0,113 1200,0 1200,12 0,125" fill="#1e73e8"/>
</svg>
<footer>
  <div class="footer-social"><i aria-label="Social link"></i><i aria-label="Social link"></i><i aria-label="Social link"></i><i aria-label="Social link"></i><i aria-label="Social link"></i></div>
  <div class="footer-links">Home<span>|</span>About us<span>|</span>Services<span>|</span>Team<span>|</span>Blog<span>|</span>Contact us</div>
  <div class="copyright">© Copyright 2018 BrightlineLabs All Rights Reserved</div>
  <div class="legal">Terms of Use<span>|</span>Privacy Policy</div>
</footer>

</body>
</html>
```